Top header for website

Header for website Size is 1000px x 120px
I have CS5 so will need the source files photoshop, illustrator etc, so I can change text and photos.
Photos attached, includes example header and screenshot of eg site
Brief:
I need a website header for golfers where I can change the photos and their name.
The header needs to have these things.
- pictures of the golfer (use from pics attached)
- Their name
- Also under there name is smaller text I need a line of text you can just say "Offical Website" in your e.g to me
so for example you should have
Colin Perrault
Offical Website
And some photos that are blended with some nice golf background or some grass or other ideas that you come up with that will look better than mine I'm sure :)
Size is 1000px x 120px
It needs to look professional and blend in nicely. I don't mind how many photos are used maybe 1-4?
The text needs to look professional too but not boring.
The header you create will be used on a website for a Professional Golfer (tour pro) their job is golf, their website needs to showcase them and promote them as best as possible.
As I said above I will need to swap photos easily and edit the text so will need the source files.
So a important point here. I guess there is no need to blend or do anything to the photos you add as I will actually need to change the photos and just need a simple template that I can swap photos and edit their name.
Ultimately I would like 3 versions of the header done and source files for all 3 so I can give them(the golfers) a choice of header type.
See how you go.
Remember that the header must have the ability for me to easily swap images and of course change the text.
My goal is to use the same header for each golfer but obviously with their images and their name.
I have CS5 so will need the source files photoshop, illustrator etc
2 example headers are attached to show you my attempts :) Please do something better.
I don't want any flash.

```html
<!DOCTYPE html>
<html lang="en">
<head>
<meta charset="utf-8">
<title>Colin Perrault — Official Website Header</title>
<link rel="stylesheet" href="https://fonts.googleapis.com/css2?family=Open+Sans:wght@300;400;700;800&display=swap">
<style>
  :root {
    --olive-deep: #2f3a06;
    --olive-mid: #5d6b0c;
    --olive-light: #8f9a14;
    --lime: #c3c925;
    --sun: #f2e23a;
    --band-top: #6ddc3a;
    --band-mid: #1f9a1c;
    --band-low: #0d6a10;
    --frame: #c9d7b0;
    --ink-light: #ffffff;
    --slot-portrait: #8a7a5e;
    --slot-portrait-low: #6f6448;
    --slot-swing: #6e7a5c;
    --slot-swing-low: #5c6649;
    --slot-bunker: #6b7434;
    --slot-bunker-low: #59622a;
  }
  html, body {
    margin: 0;
    padding: 0;
    width: 1200px;
    height: 144px;
    overflow: hidden;
    background: #ffffff;
  }
  .site-header {
    position: relative;
    width: 1200px;
    height: 144px;
    overflow: hidden;
    font-family: "Open Sans", Arial, sans-serif;
  }
  .header-backdrop {
    position: absolute;
    inset: 0;
    display: block;
  }
  .golfer-name {
    position: absolute;
    left: 40px;
    top: 37px;
    margin: 0;
    font-size: 64px;
    line-height: 64px;
    letter-spacing: -2.5px;
    color: var(--ink-light);
    text-shadow: 0 2px 3px rgba(0,0,0,0.45);
    white-space: nowrap;
  }
  .golfer-name .first-name { font-weight: 300; }
  .golfer-name .last-name { font-weight: 700; }
  .site-tagline {
    position: absolute;
    left: 40px;
    width: 454px;
    top: 106px;
    margin: 0;
    text-align: center;
    font-size: 13px;
    font-weight: 700;
    color: var(--ink-light);
    letter-spacing: 0.4px;
    text-shadow: 0 1px 2px rgba(0,0,0,0.5);
  }
  .photo-frame {
    position: absolute;
    top: 10px;
    height: 123px;
    border: 2px solid var(--frame);
    border-radius: 5px;
    box-shadow: 0 0 6px 2px rgba(0,0,0,0.55);
    box-sizing: border-box;
  }
  .photo-portrait {
    left: 564px; width: 192px;
    background: linear-gradient(180deg, var(--slot-portrait) 0%, var(--slot-portrait-low) 100%);
  }
  .photo-swing {
    left: 778px; width: 192px;
    background: linear-gradient(180deg, var(--slot-swing) 0%, var(--slot-swing-low) 100%);
  }
  .photo-bunker {
    left: 992px; width: 194px;
    background: linear-gradient(180deg, var(--slot-bunker) 0%, var(--slot-bunker-low) 100%);
  }
</style>
</head>
<body>
<header class="site-header">
  <svg class="header-backdrop" width="1200" height="144" viewBox="0 0 1200 144" aria-hidden="true">
    <defs>
      <linearGradient id="skyWash" x1="0" y1="0" x2="1" y2="0">
        <stop offset="0" stop-color="var(--olive-deep)"/>
        <stop offset="0.35" stop-color="var(--olive-mid)"/>
        <stop offset="0.55" stop-color="var(--lime)"/>
        <stop offset="1" stop-color="var(--sun)"/>
      </linearGradient>
      <linearGradient id="bandFill" x1="0" y1="0" x2="0" y2="1">
        <stop offset="0" stop-color="var(--band-top)"/>
        <stop offset="0.3" stop-color="var(--band-mid)"/>
        <stop offset="1" stop-color="var(--band-low)"/>
      </linearGradient>
      <linearGradient id="bandFade" x1="0" y1="0" x2="1" y2="0">
        <stop offset="0" stop-color="#000" stop-opacity="0.35"/>
        <stop offset="0.3" stop-color="#000" stop-opacity="0"/>
        <stop offset="1" stop-color="#000" stop-opacity="0"/>
      </linearGradient>
    </defs>
    <rect width="1200" height="144" fill="url(#skyWash)"/>
    <ellipse cx="230" cy="30" rx="330" ry="120" fill="var(--olive-light)" opacity="0.45"/>
    <ellipse cx="140" cy="150" rx="260" ry="90" fill="var(--olive-deep)" opacity="0.6"/>
    <path d="M380 144 C520 60 700 20 1200 10 L1200 0 C760 0 520 40 340 144 Z" fill="var(--sun)" opacity="0.55"/>
    <path d="M470 0 C560 40 700 60 900 50 L900 0 Z" fill="#ffffff" opacity="0.12"/>
    <rect x="0" y="45" width="1200" height="61" fill="url(#bandFill)"/>
    <rect x="0" y="45" width="1200" height="61" fill="url(#bandFade)"/>
    <rect x="0" y="45" width="1200" height="2" fill="#b6f07a" opacity="0.7"/>
    <rect x="0" y="104" width="1200" height="2" fill="#063d08" opacity="0.6"/>
  </svg>

  <h1 class="golfer-name"><span class="first-name">COLIN</span><span class="last-name">PERRAULT</span></h1>
  <p class="site-tagline">Offical Website</p>

  <div class="photo-frame photo-portrait" role="img" aria-label="Photo slot: close-up portrait of the golfer in a white cap"></div>
  <div class="photo-frame photo-swing" role="img" aria-label="Photo slot: the golfer finishing a swing at a tournament"></div>
  <div class="photo-frame photo-bunker" role="img" aria-label="Photo slot: the golfer playing a shot out of a bunker"></div>
</header>
</body>
</html>
```